Maple Grove Youngsters Guild Business Card Project

We are a Minneapolis based discount club that caters to families with children. We need a business card that can be used to communicate our contact information to other businesses that may wish to offer discounts on our website.

Please use placeholders for contact information (i.e. John Doe, 123 Any Street, Any Town, etc.) and include spaces for the following: Full name, title, email, phone number, website, one line street address, city, state, and zip code.
Updates

Project Deadline Extended
Reason: I have extended the deadline because I had not intended the project to close so quickly.

Target Market(s)

Most of the time the business cards will be used in business to business situations. However, from time to time they may be distributed to our end customer, families with children.

Industry/Entity Type

Club

Font styles to use
Serif
Sans Serif
Other font styles liked:
• Open to suggestions

Requirements
Nice to have
• We might use the reverse side of the card as the design for our membership card.

```html
<!DOCTYPE html>
<html lang="en">
<head>
<meta charset="utf-8">
<title>Maple Grove Youngsters Guild – Business Card</title>
<link href="https://fonts.googleapis.com/css2?family=Arimo:wght@400;700&display=swap" rel="stylesheet">
<style>
  :root {
    --backdrop: #544640;
    --paper: #fdfdfb;
    --name-red: #b3222d;
    --navy: #1c2a5c;
    --icon-red: #c3222e;
    --rule: #9a9a9a;
    --brand: #e8951a;
    --tone-blue: #d9ebf6;
    --tone-warm: #fbeee6;
    --tone-green: #e6f0cf;
  }
  * { box-sizing: border-box; margin: 0; padding: 0; }
  html, body {
    width: 987px; height: 1200px; overflow: hidden;
    background: var(--backdrop);
    font-family: "Arimo", Arial, sans-serif;
  }
  .canvas { position: relative; width: 987px; height: 1200px; }
  .card {
    position: absolute; width: 787px; height: 437px;
    background: var(--paper); overflow: hidden;
  }
  .card--front { left: 101px; top: 98px; }
  .card--back { left: 106px; top: 619px; }

  .wash {
    position: absolute; inset: 0;
    background: linear-gradient(90deg, var(--tone-blue) 0%, var(--paper) 30%, var(--tone-warm) 55%, var(--tone-green) 100%);
  }

  .identity { position: absolute; left: 63px; top: 112px; }
  .identity__name { color: var(--name-red); font-size: 31px; font-weight: 400; line-height: 1.1; }
  .identity__title { color: var(--navy); font-size: 18px; margin-top: 2px; }

  .contact { position: absolute; left: 62px; top: 210px; list-style: none; }
  .contact__item {
    display: flex; align-items: center; gap: 10px;
    height: 26px; color: var(--navy); font-size: 17px;
  }
  .contact__icon { width: 20px; height: 20px; flex: none; }

  .divider {
    position: absolute; left: 389px; top: 195px;
    width: 1px; height: 176px; background: var(--rule);
  }

  .brand {
    position: absolute; color: var(--brand); font-weight: 700;
    text-align: center; line-height: 1.08;
  }
  .card--front .brand { left: 440px; top: 145px; width: 280px; font-size: 38px; }
  .card--back .brand { left: 170px; top: 150px; width: 440px; font-size: 50px; }

  .website {
    position: absolute; left: 0; width: 787px; top: 400px;
    text-align: center; color: var(--icon-red); font-size: 19px;
  }
</style>
</head>
<body>
<div class="canvas">

  <section class="card card--front">
    <div class="wash" role="img" aria-label="Watercolour splash background in blue, orange, red and green"></div>

    <div class="identity">
      <h1 class="identity__name">Daniel Marsh</h1>
      <p class="identity__title">Financial Advisor</p>
    </div>

    <ul class="contact">
      <li class="contact__item">
        <svg class="contact__icon" viewBox="0 0 20 20" aria-hidden="true"><circle cx="10" cy="10" r="9" fill="none" stroke="var(--icon-red)" stroke-width="1.5"/><path d="M5 10 10 5.5 15 10h-1.8v4.5H6.8V10z" fill="var(--icon-red)"/></svg>
        482 Alder Lane
      </li>
      <li class="contact__item">
        <svg class="contact__icon" viewBox="0 0 20 20" aria-hidden="true"><circle cx="10" cy="10" r="9" fill="none" stroke="var(--icon-red)" stroke-width="1.5"/><path d="M5 10 10 5.5 15 10h-1.8v4.5H6.8V10z" fill="var(--icon-red)"/></svg>
        Oakfield, Minnesota
      </li>
      <li class="contact__item">
        <svg class="contact__icon" viewBox="0 0 20 20" aria-hidden="true"><circle cx="10" cy="10" r="9" fill="none" stroke="var(--icon-red)" stroke-width="1.5"/><rect x="5.5" y="7" width="9" height="6.5" fill="var(--icon-red)"/></svg>
        40718
      </li>
      <li class="contact__item">
        <svg class="contact__icon" viewBox="0 0 20 20" aria-hidden="true"><circle cx="10" cy="10" r="9" fill="none" stroke="var(--icon-red)" stroke-width="1.5"/><rect x="5.5" y="7" width="9" height="6.5" fill="var(--icon-red)"/><path d="M5.5 7 10 10.5 14.5 7" fill="none" stroke="#fff" stroke-width="1"/></svg>
        dan@mgyguild.com
      </li>
      <li class="contact__item">
        <svg class="contact__icon" viewBox="0 0 20 20" aria-hidden="true"><circle cx="10" cy="10" r="9" fill="none" stroke="var(--icon-red)" stroke-width="1.5"/><path d="M7 5.5c-1 .6-1.6 1.6-1 3.2 1 2.6 3 4.6 5.5 5.6 1.4.5 2.6 0 3.2-1l-1.8-1.8-1.3.8c-1.2-.6-2.2-1.6-2.8-2.8l.8-1.3z" fill="var(--icon-red)"/></svg>
        02 0147 062 318 4
      </li>
    </ul>

    <div class="divider"></div>

    <p class="brand">Maple Grove Youngsters Guild</p>
  </section>

  <section class="card card--back">
    <div class="wash" role="img" aria-label="Watercolour splash background in red, orange, blue and green"></div>
    <p class="brand">Maple Grove Youngsters Guild</p>
    <p class="website">www.maplegroveyoungstersguild.com</p>
  </section>

</div>
</body>
</html>
```